20 year old business card needs re-design

We need to redesign our corporate business card look. We need something that appears more modern, eye catchy but professional.

Target Market(s)

manufacturing industry

Industry/Entity Type

Manufacturer

Contact Information for Business Card

One side can have the logo. Other side can have contact information.

Font styles to use
Serif

Colors
3277b5
33b8a4
ffffff

Requirements
Must have
• Eye catchy - need to standout from the crowd. company logo cannot change. Full name, job title, phone number and email address.
Should not have
• Fax, business address is not necessary.

```html
<!DOCTYPE html>
<html lang="en">
<head>
<meta charset="utf-8">
<title>Norvale Industrial — Business Card</title>
<link rel="stylesheet" href="https://fonts.googleapis.com/css2?family=Montserrat:wght@400;500;700;800&display=swap">
<style>
  :root {
    --stage: #2e2e2e;
    --card-dark: #1f1d1e;
    --card-dark-2: #2a2829;
    --card-light: #ffffff;
    --brand-blue: #1f4fa3;
    --accent-teal: #33b8a4;
    --ink: #1a1a1a;
    --muted: #7a7a7a;
    --white: #ffffff;
  }
  * { box-sizing: border-box; margin: 0; padding: 0; }
  html, body { width: 1200px; height: 864px; overflow: hidden; }
  body {
    background: var(--stage);
    font-family: "Montserrat", sans-serif;
    display: flex;
    flex-direction: column;
    align-items: center;
    justify-content: center;
    gap: 40px;
  }
  .card {
    width: 630px;
    height: 360px;
    border-radius: 22px;
    position: relative;
    overflow: hidden;
    box-shadow: 0 10px 24px rgba(0,0,0,.45);
  }
  /* Front / brand side */
  .card--front { background: var(--card-dark); color: var(--white); }
  .card__texture {
    position: absolute; inset: 0;
    background: radial-gradient(ellipse at 40% 35%, var(--card-dark-2), var(--card-dark) 70%);
  }
  .brand {
    display: flex; align-items: center; gap: 12px;
    font-weight: 800; letter-spacing: -0.5px;
  }
  .brand__mark { width: 22px; height: 22px; background: var(--brand-blue); flex: none; }
  .card--front .brand {
    position: absolute; left: 50%; top: 120px; transform: translateX(-50%);
    font-size: 44px; color: var(--white); white-space: nowrap;
  }
  .tagline {
    position: absolute; left: 0; right: 0; bottom: 48px;
    text-align: center; font-size: 15px; line-height: 1.45; font-weight: 500;
  }
  .tagline__cert { font-size: 18px; }
  /* Back / contact side */
  .card--back { background: var(--card-light); color: var(--ink); }
  .card--back .brand {
    position: absolute; left: 36px; top: 166px;
    font-size: 23px; color: var(--ink); white-space: nowrap;
  }
  .card--back .brand__mark { width: 18px; height: 18px; }
  .divider {
    position: absolute; left: 318px; top: 92px; width: 2px; height: 150px;
    background: var(--brand-blue);
  }
  .contact { position: absolute; left: 340px; top: 96px; }
  .contact__name { font-size: 25px; font-weight: 700; color: var(--brand-blue); }
  .contact__title { font-size: 15px; color: var(--muted); margin-top: 2px; }
  .contact__list { list-style: none; margin-top: 28px; }
  .contact__item {
    display: flex; align-items: center; gap: 9px;
    font-size: 15px; color: #555; line-height: 1.65;
  }
  .contact__icon { width: 14px; height: 14px; flex: none; }
</style>
</head>
<body>
  <section class="card card--front">
    <div class="card__texture" role="img" aria-label="Faint engineering blueprint texture of gears and machine parts"></div>
    <div class="brand"><span class="brand__mark"></span>Norvale Industrial</div>
    <p class="tagline">
      International manufacturing solutions for OEM customers in North America<br>
      <span class="tagline__cert">TS16949 &amp; ISO9001 Certified Facilities</span>
    </p>
  </section>

  <section class="card card--back">
    <div class="brand"><span class="brand__mark"></span>Norvale Industrial</div>
    <div class="divider"></div>
    <div class="contact">
      <h1 class="contact__name">Dana Whitlock</h1>
      <p class="contact__title">Senior Project Manager</p>
      <ul class="contact__list">
        <li class="contact__item">
          <svg class="contact__icon" viewBox="0 0 16 16"><path d="M4 1.5 6.5 5 5 6.5c.8 1.8 2.6 3.7 4.5 4.5L11 9.5l3.5 2.5-1.5 2.5C7 14 2 9 1.5 3z" fill="var(--accent-teal)"/></svg>
          555-014-7720 xt 118
        </li>
        <li class="contact__item">
          <svg class="contact__icon" viewBox="0 0 16 16"><rect x="1" y="3" width="14" height="10" rx="1" fill="var(--accent-teal)"/><path d="M1.5 3.5 8 9l6.5-5.5" stroke="#fff" stroke-width="1.4" fill="none"/></svg>
          dana@norvaleindustrial.com
        </li>
        <li class="contact__item">
          <svg class="contact__icon" viewBox="0 0 16 16" fill="none" stroke="var(--accent-teal)" stroke-width="1.4"><circle cx="8" cy="8" r="6.5"/><ellipse cx="8" cy="8" rx="2.8" ry="6.5"/><path d="M1.5 8h13M2.5 4.5h11M2.5 11.5h11"/></svg>
          NorvaleIndustrial.com
        </li>
      </ul>
    </div>
  </section>
</body>
</html>
```